Brightarc Orthodontics appointment card design

I need appointment cards/ business cards made. Front will be Logo, name, title, email, phone number and location (5263 Walnut Hollow Pkwy, Ste 412, Concord, NC 28027) . the back should have an appointment card (name, time, date) and also 3 addresses listed with a check box so we can check to which location they are going.
Dale Fenwick Orthodontics
- 6735 Orchard Street, Ste 514, Harrisburg, NC 28075
- 3647 Ridgeway Drive NE, Ste 810, Concord, NC 28025
- 2917 Thornbury Corporate Drive, Ste 605, Charlotte, NC 28277
Business card can be horizontal or vertical in Design.
I need to be able to edit it to update and add new employees

Requirements
Must have
• Front:
• - Logo
• - Name & Title (able to be edited)
• - phone (704-555-0186) & Email (need to be able to edit)
• - Address: 5263 Walnut Hollow Pkwy, Ste 412
• Concord, NC 28027
• Back:
• Appointment Card design:
• - Name, time, Date
• - 3 locations w/ a check box so the patient knows where to go:
• Dale Fenwick Orthodontics
• - 6735 Orchard Street, Ste 514, Harrisburg, NC 28075
• - 3647 Ridgeway Drive NE, Ste 810, Concord, NC 28025
• - 2917 Thornbury Corporate Drive, Ste 605, Charlotte, NC 28277

```html
<!DOCTYPE html>
<html lang="en">
<head>
<meta charset="utf-8">
<title>Brightarc Orthodontics – Appointment &amp; Business Card</title>
<link rel="stylesheet" href="https://fonts.googleapis.com/css2?family=Roboto:wght@400;500;700;900&display=swap">
<style>
  :root {
    --stage: #3a3b3e;
    --card: #ffffff;
    --brand-blue: #2f7fb8;
    --brand-blue-deep: #1f6fb0;
    --ink: #444a50;
    --ink-soft: #5c6268;
    --rule: #4a4f55;
    --divider: #7a7c80;
  }
  * { box-sizing: border-box; margin: 0; padding: 0; }
  html, body { width: 1200px; height: 1000px; overflow: hidden; }
  body {
    background: var(--stage);
    font-family: "Roboto", Arial, sans-serif;
    color: var(--ink);
    position: relative;
  }
  .card {
    position: absolute;
    left: 220px;
    width: 760px;
    height: 434px;
    background: var(--card);
    border-radius: 26px;
    overflow: hidden;
    box-shadow: 0 10px 24px rgba(0,0,0,.35);
  }

  /* ---------- appointment side ---------- */
  .appointment { top: 50px; }
  .appointment .top-band {
    position: absolute; left: 0; top: 0; width: 100%; height: 14px;
    background: var(--brand-blue-deep);
  }
  .appointment .heading {
    position: absolute; left: 40px; top: 50px;
    font-size: 22px; font-weight: 700; color: var(--brand-blue-deep);
  }
  .field {
    position: absolute; display: flex; align-items: flex-end; gap: 8px;
    font-size: 15px; color: var(--ink-soft);
  }
  .field .line { flex: 1; border-bottom: 1.5px solid var(--rule); height: 1px; }
  .field-name { left: 40px; top: 104px; width: 400px; }
  .field-date { left: 40px; top: 146px; width: 400px; }
  .field-time { left: 300px; top: 196px; width: 420px; }
  .ampm {
    position: absolute; left: 560px; top: 236px;
    display: flex; gap: 26px; font-size: 15px; color: var(--ink-soft);
  }
  .ampm span { display: flex; align-items: center; gap: 6px; }
  .box {
    display: inline-block; width: 15px; height: 15px;
    border: 1.8px solid var(--brand-blue-deep); background: #fff;
  }
  .appointment .wordmark {
    position: absolute; right: 40px; top: 100px;
    display: flex; align-items: center; gap: 10px;
    font-size: 24px; font-weight: 700; color: var(--brand-blue-deep);
  }
  .dot { width: 16px; height: 16px; border-radius: 50%; background: var(--brand-blue-deep); }
  .practice {
    position: absolute; left: 0; width: 100%; top: 272px; text-align: center;
    font-size: 21px; font-weight: 700; color: var(--brand-blue-deep);
  }
  .practice small { font-size: 16px; font-weight: 400; color: var(--ink); }
  .locations {
    position: absolute; left: 30px; right: 30px; top: 318px;
    display: flex; justify-content: space-between; text-align: center;
  }
  .location { width: 220px; font-size: 13.5px; line-height: 1.3; color: var(--ink); }
  .location .box { margin-bottom: 8px; }

  /* ---------- business side ---------- */
  .business { top: 516px; }
  .business .brand-side {
    position: absolute; left: 0; top: 0; width: 400px; height: 100%;
    display: flex; align-items: center; justify-content: center; gap: 12px;
  }
  .business .brand-side .wordmark {
    font-size: 32px; font-weight: 700; color: var(--brand-blue-deep); line-height: 1.1;
  }
  .business .brand-side .dot { width: 22px; height: 22px; }
  .business .divider {
    position: absolute; left: 400px; top: 0; width: 14px; height: 100%;
    background: var(--divider);
  }
  .business .contact-side {
    position: absolute; left: 414px; top: 0; right: 0; height: 100%;
    background: var(--brand-blue); color: #fff;
    padding: 112px 0 0 40px;
  }
  .person { font-size: 22px; font-weight: 700; letter-spacing: .3px; }
  .title { font-size: 16px; margin-top: 2px; }
  .address { font-size: 15px; line-height: 1.35; margin-top: 18px; }
  .contact-row { display: flex; align-items: center; gap: 10px; font-size: 16px; margin-top: 8px; }
  .contact-row svg { width: 14px; height: 14px; flex: none; }
</style>
</head>
<body>

  <section class="card appointment" aria-label="Appointment card">
    <div class="top-band"></div>
    <h2 class="heading">Next Appointment</h2>

    <div class="field field-name">Name <span class="line"></span></div>
    <div class="field field-date">Date <span class="line"></span></div>
    <div class="field field-time">Time <span class="line"></span></div>
    <div class="ampm">
      <span><i class="box"></i>AM</span>
      <span><i class="box"></i>PM</span>
    </div>

    <div class="wordmark"><span class="dot"></span>Brightarc Orthodontics</div>

    <p class="practice">Dale Fenwick <small>Orthodontics</small></p>

    <div class="locations">
      <div class="location"><i class="box"></i><br>6735 Orchard Street, Ste 514,<br>Harrisburg, NC 28075</div>
      <div class="location"><i class="box"></i><br>3647 Ridgeway Drive NE, Ste 810,<br>Concord, NC 28025</div>
      <div class="location"><i class="box"></i><br>2917 Thornbury Corporate Drive,<br>Ste 605, Charlotte, NC 28277</div>
    </div>
  </section>

  <section class="card business" aria-label="Business card">
    <div class="brand-side">
      <span class="dot"></span>
      <span class="wordmark">Brightarc<br>Orthodontics</span>
    </div>
    <div class="divider"></div>
    <div class="contact-side">
      <p class="person">DALE FENWICK</p>
      <p class="title">Orthodontics</p>
      <p class="address">5263 Walnut Hollow Pkwy,<br>Ste 412 - Concord, NC 28027</p>
      <p class="contact-row">
        <svg viewBox="0 0 16 16" aria-hidden="true"><path fill="#fff" d="M3.5 1.5l2.5 0 1 3.5-1.6 1.2a9 9 0 0 0 4.4 4.4L11 9l3.5 1v2.5c0 1-1 2-2 2A11 11 0 0 1 1.5 3.5c0-1 1-2 2-2z"/></svg>
        704-555-0186
      </p>
      <p class="contact-row">
        <svg viewBox="0 0 16 16" aria-hidden="true"><rect x="1" y="3" width="14" height="10" rx="1" fill="#fff"/><path d="M1.5 3.5L8 9l6.5-5.5" stroke="#2f7fb8" stroke-width="1.4" fill="none"/></svg>
        dale.fenwick@brightarcmail.com
      </p>
    </div>
  </section>

</body>
</html>
```